Web design for financial services

A modern web design of financial services (brokerage firm)
Req.s and technology tags :
- Very mobile friendly.
- One paged with some inner pages.
- Animated sticky header .
- Member login area for e-trade.
- Support RTL language.
- HTML & CSS.

The logo will be Home link
• MPTR :
WHO WE ARE
Content :
i) Board of Directors
ii) Mission Statement
iii) Corporate Values
iv) Regulations
• Financial Services :
WHAT WE DO
Content:
i) Electronic trading
ii) Trading desk
iii) Institutional
iv) Investors Education
• News
• Market Tools
• Forms---- opens new page
• Careers---- opens new page
• Contact Us----opens new page

The website is :
http://www.mptr-doha-example.com/

The logo need some changes to be more modern and impressively , but with keeping same structure .

Some related websites :
https://www.lv-bourse.example/

financial market

Financial Service

Coded - Design and coding required

2 page

• same fonts of http://www.kwdholdings.example/

• - Very mobile friendly.
• - One paged with some inner pages.
• - Animated sticky header .
• - Member login area for e-trade.
• - Support RTL language.
• - HTML & CSS.
• Slider , some Qatari theme,
• i like the video inside the home page
• ex :http://www.kwdholdings.example/

```html
<!DOCTYPE html>
<html lang="en">
<head>
<meta charset="utf-8">
<title>MPTR — Financial Services</title>
<link rel="stylesheet" href="https://fonts.googleapis.com/css2?family=Jost:wght@400;500;600&family=Open+Sans:wght@400;600;700&display=swap">
<style>
:root{
  --brand:#9b2a25;
  --brand-dark:#7f211d;
  --ink:#1d1d1d;
  --text:#4a4a4a;
  --muted:#6d6d6d;
  --band:#e6e7e9;
  --line:#d7d7d7;
  --white:#ffffff;
}
*{box-sizing:border-box;margin:0;padding:0}
html,body{width:1200px;height:4313px;overflow:hidden}
body{position:relative;background:var(--white);font-family:"Open Sans",Arial,sans-serif;color:var(--text)}
.abs{position:absolute}
.heading{font-family:"Jost",Arial,sans-serif;font-weight:400;color:var(--brand);font-size:38px;letter-spacing:.5px;line-height:1}
.btn-outline{position:absolute;border:1px solid var(--brand);color:var(--brand);font-size:12px;display:flex;align-items:center;justify-content:center;gap:6px;text-transform:uppercase;letter-spacing:.3px}

/* hero */
.hero{position:absolute;left:0;top:0;width:1200px;height:718px;background:linear-gradient(180deg,#3a8fd6 0%,#7fb6e3 30%,#c9b89a 55%,#6d6a62 75%,#3f4750 100%)}
.brand-mark{position:absolute;display:flex;align-items:center;gap:12px;font-family:"Jost",Arial,sans-serif;font-weight:600;color:var(--ink);letter-spacing:2px}
.brand-mark .dot{width:22px;height:22px;background:var(--brand)}
.hero .brand-mark{left:132px;top:96px;font-size:52px;color:#2a2a2a}
.nav{position:absolute;top:36px;left:393px;display:flex;gap:0;font-size:13px;color:var(--ink)}
.nav a{color:#1d1d1d;text-decoration:none;position:absolute;white-space:nowrap}
.login{position:absolute;left:882px;top:29px;width:84px;height:32px;background:var(--brand);color:#fff;font-size:12px;display:flex;align-items:center;justify-content:center;gap:7px;font-weight:600}
.lang{position:absolute;left:973px;top:29px;width:94px;height:32px;border:1px solid #fff;color:#fff;font-size:11px;display:flex;align-items:center;justify-content:center;gap:6px}
.lang .flag{width:16px;height:11px;background:#d9d9d9}
.play{position:absolute;left:536px;top:298px}
.hero-title{position:absolute;left:0;width:1200px;top:588px;text-align:center;font-family:"Jost",Arial,sans-serif;font-weight:600;font-size:38px;color:#fff;letter-spacing:1px}

/* who we are */
.about-text{position:absolute;left:130px;top:846px;width:333px;font-size:13.5px;line-height:25.5px;text-align:justify;color:#333}
.sub-heading{font-family:"Jost",Arial,sans-serif;font-weight:600;color:var(--brand);font-size:17px}
.mission-text{position:absolute;left:130px;top:1070px;width:333px;font-size:12px;line-height:22.5px;text-align:justify;color:#333}
.tower-photo{position:absolute;left:653px;top:911px;width:308px;height:308px;border-radius:50%;background:radial-gradient(circle at 55% 40%,#8b6fb8 0%,#3e4f86 45%,#1f2e55 100%)}

/* what we do */
.band{position:absolute;left:0;width:1200px;background:var(--band)}
.consult-art{position:absolute;left:121px;top:1473px;width:468px;height:468px;border-radius:50%;background:radial-gradient(circle,#f3f3f4 0%,#e9eaec 70%,#e6e7e9 100%)}
.service{position:absolute;left:686px;width:380px}
.service .icon{position:absolute;left:0;top:0;width:62px;height:62px;border-radius:50%;background:var(--brand);display:flex;align-items:center;justify-content:center}
.service h3{position:absolute;left:82px;top:0;font-family:"Jost",Arial,sans-serif;font-weight:400;font-size:15px;color:var(--brand);text-transform:uppercase}
.service p{position:absolute;left:82px;top:26px;width:290px;font-size:11.5px;line-height:21px;color:#555}

/* news */
.news-card{position:absolute;top:2221px;width:264px}
.news-card .photo{width:264px;height:153px;background:linear-gradient(135deg,#c9ccd1,#7b8089 60%,#3e4249)}
.news-card.blue .photo{background:linear-gradient(135deg,#e8eef5,#9fb7d3 55%,#5674a0)}
.news-card.dark .photo{background:linear-gradient(135deg,#d6d7d9,#6a6d72 50%,#2a2d32)}
.news-card .date{position:absolute;left:10px;top:138px;background:#fff;border:1px solid var(--line);font-size:9px;padding:3px 8px;color:#333}
.news-card h3{margin-top:38px;font-family:"Open Sans",Arial,sans-serif;font-weight:600;font-size:16.5px;line-height:28px;color:var(--ink)}
.news-card p{margin-top:20px;font-size:12.5px;line-height:24px;color:#555;padding-left:2px}
.news-card .more{margin-top:20px;font-size:11px;color:var(--brand);display:flex;align-items:center;gap:10px;padding-left:2px}

/* testimonials */
.quote-card{position:absolute;top:2896px;height:231px;background:#fff;text-align:center}
.quote-card .avatar{position:absolute;top:-28px;left:50%;margin-left:-29px;width:58px;height:58px;border-radius:50%;background:linear-gradient(180deg,#c9c3bb,#6d6a66);border:2px solid #fff}
.quote-card p{position:absolute;top:66px;left:50px;right:50px;font-size:12.5px;line-height:24px;color:#333}
.quote-card .name{position:absolute;bottom:0;left:50%;transform:translateX(-50%);background:var(--brand);color:#fff;font-size:9px;font-weight:700;padding:5px 12px;white-space:nowrap;text-transform:uppercase}
.quote-card .name span{font-weight:400;text-transform:none}

/* market tools */
.tool-box{position:absolute;top:3360px;height:470px;border:1px solid var(--line);background:#fff}
.tool-box h3{position:absolute;left:27px;top:30px;font-family:"Open Sans",Arial,sans-serif;font-weight:600;font-size:15.5px;color:var(--ink)}
.tool-item{position:absolute;left:27px;right:10px}
.tool-item svg{position:absolute;left:0;top:2px}
.tool-item h4{position:absolute;left:32px;top:0;font-weight:400;font-size:13px;color:var(--brand);white-space:nowrap}
.tool-item p{position:absolute;left:32px;top:24px;width:210px;font-size:11px;line-height:20px;color:#555}

/* footer */
.footer .brand-mark{left:172px;top:4040px;font-size:48px}
.foot-title{position:absolute;font-size:10.5px;font-weight:700;color:var(--brand);text-transform:uppercase}
.contact-row{position:absolute;left:425px;width:260px;font-size:10.5px;line-height:22px;color:#444}
.contact-row svg{position:absolute;left:0;top:4px}
.contact-row span{position:absolute;left:32px;top:0}
.email-field{position:absolute;left:748px;top:4018px;width:318px;height:47px;background:#fff;font-size:11px;color:#444;display:flex;align-items:center;gap:14px;padding-left:17px}
.signup{position:absolute;left:961px;top:4081px;width:104px;height:39px;background:var(--brand);color:#fff;font-size:13px;font-weight:700;display:flex;align-items:center;justify-content:center}
.social{position:absolute;top:4254px;width:26px;height:26px;border-radius:50%;background:var(--brand)}
</style>
</head>
<body>

<header class="hero" role="img" aria-label="Photo of a city skyline with glass towers along a river at sunset">
  <div class="brand-mark"><span class="dot"></span>MPTR</div>
  <nav class="nav">
    <a style="left:0">MPTR</a>
    <a style="left:61px">Financial Service</a>
    <a style="left:193px">News</a>
    <a style="left:255px">Market Tool</a>
    <a style="left:356px">Forms</a>
    <a style="left:420px">Careers</a>
  </nav>
  <div class="login">
    <svg width="10" height="11" viewBox="0 0 10 11"><rect x="1" y="5" width="8" height="6" fill="#fff"/><path d="M3 5V3a2 2 0 0 1 4 0v2" stroke="#fff" stroke-width="1.4" fill="none"/></svg>LOGIN
  </div>
  <div class="lang"><span class="flag"></span>English
    <svg width="8" height="5" viewBox="0 0 8 5"><path d="M0 0h8L4 5z" fill="#fff"/></svg>
  </div>
  <svg class="play" width="126" height="126" viewBox="0 0 126 126">
    <circle cx="63" cy="63" r="58" fill="none" stroke="rgba(255,255,255,.75)" stroke-width="6"/>
    <path d="M50 38 L90 63 L50 88 Z" fill="rgba(255,255,255,.75)"/>
  </svg>
  <h1 class="hero-title">FINANCIAL SERVICES</h1>
</header>

<section class="who">
  <h2 class="heading abs" style="left:130px;top:784px">WHO WE ARE</h2>
  <p class="about-text">Meridian Pearl Trading Reserve is a Private Qatari company that aims to provide secure and technologically advanced methods of trading to its clients. Those facilities enables clients to trade faster, more secure &amp; private. Having this strategy in our in minds, with this online portal we begin.</p>
  <h3 class="sub-heading abs" style="left:130px;top:1032px">OUR MISION</h3>
  <p class="mission-text">We intent to optimize all company resources to position ourselves as an unique competitive business model with the goal of generating highly competitive returns for our clients and shareholders, by providing accurate, rapid and reliable order execution, attractive financial products and services, sophisticated customer service by investing and implementing state of the art technology always in line with compliance to regulatory rules and regulations..</p>
  <div class="btn-outline" style="left:134px;top:1287px;width:110px;height:37px">ABOUT MPTR</div>
  <div class="tower-photo" role="img" aria-label="Photo of a lit skyscraper at dusk"></div>
</section>

<section class="band" style="top:1398px;height:654px">
  <div class="consult-art" style="top:75px" role="img" aria-label="Line illustration about business consulting: projects, team, results, strategy and success"></div>
  <h2 class="heading abs" style="left:686px;top:64px">WHAT WE DO</h2>
  <p class="abs" style="left:686px;top:119px;width:362px;font-size:13px;line-height:25.5px;text-align:justify;color:#333">There are many variations of passages of Lorem Ipsum available, but the majority have suffered alteration in some form, by injected humour, or randomised words which don't look even slightly believable. If you are going to use a passage of Lorem Ipsum, you need to be sure there isn't anything.</p>
  <div class="service" style="top:320px">
    <div class="icon"><svg width="30" height="30" viewBox="0 0 30 30"><circle cx="17" cy="11" r="7" fill="none" stroke="#fff" stroke-width="2"/><path d="M17 7v8M15 9h4M15 13h4" stroke="#fff" stroke-width="1.5"/><path d="M3 24h6l5 2h8l5-4" stroke="#fff" stroke-width="2" fill="none"/></svg></div>
    <h3>Financial Services</h3>
    <p>There are many variations of passages of Lorem Ipsum available, but the.</p>
  </div>
  <div class="service" style="top:434px">
    <div class="icon"><svg width="32" height="26" viewBox="0 0 32 26"><circle cx="16" cy="7" r="4" fill="#fff"/><circle cx="7" cy="10" r="3" fill="#fff"/><circle cx="25" cy="10" r="3" fill="#fff"/><path d="M10 22a6 6 0 0 1 12 0z M2 22a5 5 0 0 1 8-3v3z M30 22a5 5 0 0 0-8-3v3z" fill="#fff"/></svg></div>
    <h3>Team</h3>
    <p>It is a long established fact that a reader will be distracted by the readable content of a page.</p>
  </div>
  <div class="btn-outline" style="left:691px;top:549px;width:111px;height:37px">READ MORE
    <svg width="5" height="8" viewBox="0 0 5 8"><path d="M0 0l5 4-5 4z" fill="#9b2a25"/></svg></div>
</section>

<section class="news">
  <h2 class="heading abs" style="left:129px;top:2130px">LATEST NEWS</h2>
  <div class="btn-outline" style="left:947px;top:2151px;width:121px;height:35px;font-size:11px">VIEW ALL NEWS
    <svg width="5" height="8" viewBox="0 0 5 8"><path d="M0 0l5 4-5 4z" fill="#9b2a25"/></svg></div>
  <article class="news-card" style="left:132px">
    <div class="photo" role="img" aria-label="Photo of hands writing beside a laptop"></div>
    <span class="date">01 FEB, 2017</span>
    <h3>There are many variations of pas sages of Lorem Ipsum.</h3>
    <p>It is a long established fact that a reader will be distracted by the readable content of a page when looking.</p>
    <div class="more">CONTINUE READING <svg width="16" height="8" viewBox="0 0 16 8"><path d="M0 4h13M10 1l4 3-4 3" stroke="#9b2a25" stroke-width="1.5" fill="none"/></svg></div>
  </article>
  <article class="news-card blue" style="left:467px">
    <div class="photo" role="img" aria-label="Photo of a hand using a calculator over financial charts"></div>
    <span class="date">01 FEB, 2017</span>
    <h3>It is a long established fact that a reader will be distracted.</h3>
    <p>But I must explain to you how all this mistaken idea of denouncing pleasure and praising.</p>
    <div class="more">CONTINUE READING <svg width="16" height="8" viewBox="0 0 16 8"><path d="M0 4h13M10 1l4 3-4 3" stroke="#9b2a25" stroke-width="1.5" fill="none"/></svg></div>
  </article>
  <article class="news-card dark" style="left:804px">
    <div class="photo" role="img" aria-label="Photo of hands typing on a laptop showing market charts"></div>
    <span class="date">01 FEB, 2017</span>
    <h3>On the other hand, we denounce with righteous indignation.</h3>
    <p>At vero eos et accusamus et iusto odio dignissimos ducimus qui blanditiis praesentium voluptatum.</p>
    <div class="more">CONTINUE READING <svg width="16" height="8" viewBox="0 0 16 8"><path d="M0 4h13M10 1l4 3-4 3" stroke="#9b2a25" stroke-width="1.5" fill="none"/></svg></div>
  </article>
</section>

<section class="band" style="top:2700px;height:501px">
  <h2 class="heading abs" style="left:130px;top:68px">TESTIMONIALS</h2>
  <svg class="abs" style="left:1002px;top:72px" width="64" height="30" viewBox="0 0 64 30">
    <path d="M16 3L6 15l10 12" stroke="#a9a9ad" stroke-width="3" fill="none"/>
    <path d="M48 3l10 12-10 12" stroke="#a9a9ad" stroke-width="3" fill="none"/>
  </svg>
</section>
<div class="quote-card" style="left:132px;width:296px">
  <div class="avatar" role="img" aria-label="Client portrait"></div>
  <p>At vero eos et accusamus et iusto odio dignissimos ducimus qui blanditiis praesentium. sint occaecati cupiditate non provident.</p>
  <div class="name">Martin Calloway, <span>England</span></div>
</div>
<div class="quote-card" style="left:450px;width:295px">
  <div class="avatar" role="img" aria-label="Client portrait"></div>
  <p>But I must explain to you how all this mistaken idea of denouncing pleasure and praising pain was born and I will give you a complete.</p>
  <div class="name">Jonah, <span>England</span></div>
</div>
<div class="quote-card" style="left:770px;width:296px">
  <div class="avatar" role="img" aria-label="Client portrait"></div>
  <p>On the other hand, we denounce with righteous indignation and dislike men who are so beguiled and demoralized by the charms .</p>
  <div class="name">Corwin, <span>England</span></div>
</div>

<section class="tools">
  <h2 class="heading abs" style="left:130px;top:3270px">MARKET TOOLS</h2>

  <div class="tool-box" style="left:131px;width:303px">
    <h3>Most Active Company</h3>
    <div class="tool-item" style="top:92px"><svg width="14" height="14" viewBox="0 0 14 14"><circle cx="7" cy="7" r="6" fill="none" stroke="#9b2a25" stroke-width="1.5"/><path d="M5.5 4.5L8 7l-2.5 2.5" stroke="#9b2a25" stroke-width="1.5" fill="none"/></svg><h4>Sed ut perspiciatis unde omnis</h4><p>On the other hand, we denounce with righteous indignation.</p></div>
    <div class="tool-item" style="top:186px"><svg width="14" height="14" viewBox="0 0 14 14"><circle cx="7" cy="7" r="6" fill="none" stroke="#9b2a25" stroke-width="1.5"/><path d="M5.5 4.5L8 7l-2.5 2.5" stroke="#9b2a25" stroke-width="1.5" fill="none"/></svg><h4>At vero eos et accusamus</h4><p>Et harum quidem rerum facilis est et expedita distinctio. Nam libero</p></div>
    <div class="tool-item" style="top:286px"><svg width="14" height="14" viewBox="0 0 14 14"><circle cx="7" cy="7" r="6" fill="none" stroke="#9b2a25" stroke-width="1.5"/><path d="M5.5 4.5L8 7l-2.5 2.5" stroke="#9b2a25" stroke-width="1.5" fill="none"/></svg><h4>But I must explain to you how</h4><p>Nor again is there anyone who loves or pursues or desires to .</p></div>
    <div class="tool-item" style="top:385px"><svg width="14" height="14" viewBox="0 0 14 14"><circle cx="7" cy="7" r="6" fill="none" stroke="#9b2a25" stroke-width="1.5"/><path d="M5.5 4.5L8 7l-2.5 2.5" stroke="#9b2a25" stroke-width="1.5" fill="none"/></svg><h4>On the other hand we denounce</h4><p>They cannot foresee the pain and trouble that are bound to ensue</p></div>
  </div>

  <div class="tool-box" style="left:449px;width:296px">
    <h3>Top Gainer</h3>
    <div class="tool-item" style="top:92px"><svg width="14" height="14" viewBox="0 0 14 14"><circle cx="7" cy="7" r="6" fill="none" stroke="#9b2a25" stroke-width="1.5"/><path d="M5.5 4.5L8 7l-2.5 2.5" stroke="#9b2a25" stroke-width="1.5" fill="none"/></svg><h4>Lorem ipsum dolor sit amet</h4><p>On the other hand, we denounce with righteous indignation.</p></div>
    <div class="tool-item" style="top:186px"><svg width="14" height="14" viewBox="0 0 14 14"><circle cx="7" cy="7" r="6" fill="none" stroke="#9b2a25" stroke-width="1.5"/><path d="M5.5 4.5L8 7l-2.5 2.5" stroke="#9b2a25" stroke-width="1.5" fill="none"/></svg><h4>Consectetur adipisci velit</h4><p>Et harum quidem rerum facilis est et expedita distinctio. Nam libero</p></div>
    <div class="tool-item" style="top:286px"><svg width="14" height="14" viewBox="0 0 14 14"><circle cx="7" cy="7" r="6" fill="none" stroke="#9b2a25" stroke-width="1.5"/><path d="M5.5 4.5L8 7l-2.5 2.5" stroke="#9b2a25" stroke-width="1.5" fill="none"/></svg><h4>Nam libero tempore cum</h4><p>Nor again is there anyone who loves or pursues or desires to .</p></div>
    <div class="tool-item" style="top:385px"><svg width="14" height="14" viewBox="0 0 14 14"><circle cx="7" cy="7" r="6" fill="none" stroke="#9b2a25" stroke-width="1.5"/><path d="M5.5 4.5L8 7l-2.5 2.5" stroke="#9b2a25" stroke-width="1.5" fill="none"/></svg><h4>In a free hour when our</h4><p>They cannot foresee the pain and trouble that are bound to ensue</p></div>
  </div>

  <div class="tool-box" style="left:770px;width:296px">
    <h3>Top Loser</h3>
    <div class="tool-item" style="top:92px"><svg width="14" height="14" viewBox="0 0 14 14"><circle cx="7" cy="7" r="6" fill="none" stroke="#9b2a25" stroke-width="1.5"/><path d="M5.5 4.5L8 7l-2.5 2.5" stroke="#9b2a25" stroke-width="1.5" fill="none"/></svg><h4>It uses a dictionary of over</h4><p>On the other hand, we denounce with righteous indignation.</p></div>
    <div class="tool-item" style="top:186px"><svg width="14" height="14" viewBox="0 0 14 14"><circle cx="7" cy="7" r="6" fill="none" stroke="#9b2a25" stroke-width="1.5"/><path d="M5.5 4.5L8 7l-2.5 2.5" stroke="#9b2a25" stroke-width="1.5" fill="none"/></svg><h4>At vero eos et accusamus</h4><p>Et harum quidem rerum facilis est et expedita distinctio. Nam libero</p></div>
    <div class="tool-item" style="top:286px"><svg width="14" height="14" viewBox="0 0 14 14"><circle cx="7" cy="7" r="6" fill="none" stroke="#9b2a25" stroke-width="1.5"/><path d="M5.5 4.5L8 7l-2.5 2.5" stroke="#9b2a25" stroke-width="1.5" fill="none"/></svg><h4>But I must explain to you how</h4><p>Nor again is there anyone who loves or pursues or desires to .</p></div>
    <div class="tool-item" style="top:385px"><svg width="14" height="14" viewBox="0 0 14 14"><circle cx="7" cy="7" r="6" fill="none" stroke="#9b2a25" stroke-width="1.5"/><path d="M5.5 4.5L8 7l-2.5 2.5" stroke="#9b2a25" stroke-width="1.5" fill="none"/></svg><h4>On the other hand we denounce</h4><p>They cannot foresee the pain and trouble that are bound to ensue</p></div>
  </div>
</section>

<footer class="footer">
  <div class="band" style="top:3887px;height:426px"></div>
  <div class="brand-mark"><span class="dot"></span>MPTR</div>

  <div class="foot-title" style="left:425px;top:3952px">Contact Us</div>
  <div class="contact-row" style="top:3998px;height:44px">
    <svg width="12" height="15" viewBox="0 0 12 15"><path d="M6 0a6 6 0 0 1 6 6c0 4-6 9-6 9S0 10 0 6a6 6 0 0 1 6-6z" fill="#9b2a25"/><circle cx="6" cy="6" r="2.2" fill="#e6e7e9"/></svg>
    <span style="width:225px">Second Floor, Sidra Court, Harbour Row near Palm Plaza</span>
  </div>
  <div class="contact-row" style="top:4059px">
    <svg width="13" height="13" viewBox="0 0 13 13"><path d="M3 0l2.5 3-1.5 2a8 8 0 0 0 4 4l2-1.5L13 10l-2 3C5 13 0 8 0 2z" fill="#9b2a25"/></svg>
    <span>+974 40000000</span>
  </div>
  <div class="contact-row" style="top:4096px">
    <svg width="13" height="10" viewBox="0 0 13 10"><rect width="13" height="10" fill="#9b2a25"/><path d="M0 0l6.5 5L13 0" stroke="#e6e7e9" stroke-width="1.2" fill="none"/></svg>
    <span>hello@mptr-doha-example.com</span>
  </div>

  <div class="foot-title" style="left:747px;top:3951px">Newsletter Signup!</div>
  <div class="abs" style="left:747px;top:3978px;font-size:10.5px;color:#444">Get more details to signup!</div>
  <div class="email-field">
    <svg width="13" height="10" viewBox="0 0 13 10"><rect x=".6" y=".6" width="11.8" height="8.8" fill="none" stroke="#444" stroke-width="1.2"/><path d="M.6.6l5.9 4.6L12.4.6" stroke="#444" stroke-width="1.2" fill="none"/></svg>
    E mail id
  </div>
  <div class="signup">SIGNUP!</div>

  <div class="abs" style="left:0;top:4214px;width:1200px;height:1px;background:#d2d3d6"></div>
  <div class="foot-title" style="left:130px;top:4262px">Follow Us</div>
  <span class="social" style="left:216px" aria-label="Social link"></span>
  <span class="social" style="left:252px" aria-label="Social link"></span>
  <span class="social" style="left:288px" aria-label="Social link"></span>
  <div class="abs" style="left:880px;top:4263px;width:186px;text-align:right;font-size:10.5px;color:#444">Copyrights @ 2017 All Rights Reserved</div>
</footer>

</body>
</html>
```